Fenwick Grading LTD - website for irrigation & Landscape Lighting & Buried service wire

Looking for a website to help promote my business with Irrigation (installation, service, etc) and buried service wire/drainage solutions.

Commercial/Residential

Landscape lighting.

I’ll get photos in the trucks and trailers to upload as well maybe the machine as well.

Target Market(s)

Homeowners who want green grass and beautiful gardens. Beautiful landscape lighting

Industry/Entity Type

Irrigation systems and landscape lighting and buried service wire to homes and offering Drainage soltions.

Coding

Coded - Design and coding required

Number of Pages Required

4 page

Colors
F0912C
F2A743
F7CA91
FBE8D2
FDF5EE

Requirements
Must have
• was hoping to link up my email on fenwickgrading@mailbox-example.net with the website if possible.
Nice to have
• Page for Irrigation, page for landscape lighting, page buried service wire & drainage soltions.

```html
<!DOCTYPE html>
<html lang="en">
<head>
<meta charset="utf-8">
<title>Fenwick Grading LTD</title>
<link rel="stylesheet" href="https://fonts.googleapis.com/css2?family=Montserrat:wght@600;700;800&family=Roboto:ital,wght@0,400;0,500;0,700;1,400&display=swap">
<style>
:root{
  --orange:#F0912C;
  --orange-2:#F2A743;
  --orange-3:#F7CA91;
  --cream:#FBE8D2;
  --cream-2:#FDF5EE;
  --ink:#141414;
  --text:#6b6b6b;
  --grey-ring:#808080;
  --footer:#1d1d1f;
  --white:#ffffff;
}
*{margin:0;padding:0;box-sizing:border-box}
html,body{width:1200px;height:4402px;overflow:hidden}
body{position:relative;background:var(--white);font-family:'Roboto',Arial,sans-serif;color:var(--ink)}
.abs{position:absolute}
.photo{position:absolute;display:block}
.heading{font-family:'Montserrat',Arial,sans-serif;font-weight:700;color:var(--ink);letter-spacing:.5px}
.section-title{position:absolute;left:0;width:1200px;text-align:center;font-size:38px}
.title-rule{position:absolute;left:568px;width:64px;height:4px;background:var(--orange);border-radius:2px}
.btn{position:absolute;display:flex;align-items:center;justify-content:center;gap:6px;background:var(--orange);color:var(--white);font-family:'Roboto',Arial,sans-serif;font-weight:700;font-size:13px;border-radius:24px;text-transform:uppercase;letter-spacing:.2px}
.btn .chev{width:12px;height:12px}

/* hero */
.hero{left:0;top:0;width:1200px;height:723px;background:linear-gradient(180deg,#4a6783 0%,#7f8b99 30%,#c99a72 50%,#e0a266 58%,#4b5a33 76%,#2c3a1d 100%)}
.brand{left:111px;top:44px;color:var(--white);font-family:'Montserrat',Arial,sans-serif;font-weight:700;line-height:1}
.brand .name{font-size:30px;letter-spacing:1px}
.brand .sub{font-size:14px;letter-spacing:2.4px;margin-top:4px}
.nav{left:429px;top:37px;color:var(--white);font-size:14px}
.nav a{position:absolute;color:var(--white);text-decoration:none;white-space:nowrap}
.nav .active::before{content:"";position:absolute;left:0;top:-16px;width:38px;height:3px;background:var(--orange)}
.call{left:805px;top:0;width:284px;height:92px;background:var(--orange);clip-path:polygon(34px 0,100% 0,100% 100%,0 100%);color:var(--white)}
.call .ring{position:absolute;left:48px;top:28px;width:36px;height:36px;border-radius:50%;background:var(--white)}
.call .lbl{position:absolute;left:96px;top:27px;font-size:13px}
.call .num{position:absolute;left:96px;top:43px;font-size:20px;font-weight:700;letter-spacing:.5px;white-space:nowrap}
.hero-title{left:111px;top:252px;color:var(--white);font-size:52px;line-height:68px;letter-spacing:1.5px}
.hero-btn{left:111px;top:397px;width:162px;height:47px}
.slider-arrows{left:110px;top:640px}

/* about */
.about-main{left:234px;top:832px;width:528px;height:376px;background:linear-gradient(160deg,#38475a 0%,#6b6a6c 40%,#a7938a 65%,#bfb7ad 100%)}
.about-small{left:111px;top:1020px;width:327px;height:266px;background:linear-gradient(170deg,#7d94a8 0%,#4b5040 55%,#2a3c4c 100%);border:4px solid var(--white)}
.badge{left:172px;top:866px;width:124px;height:124px;border-radius:50%;background:var(--orange);border:5px solid var(--white);color:var(--white);text-align:center;padding-top:26px;line-height:1.15}
.badge b{font-family:'Montserrat',Arial,sans-serif;font-size:27px;display:block}
.badge span{font-size:14px;display:block}
.about-box{left:619px;top:914px;width:500px;height:390px;background:var(--white)}
.about-title{left:648px;top:932px;font-size:40px}
.about-rule{left:648px;top:991px;width:63px;height:4px;background:var(--orange)}
.about-copy{left:648px;top:1014px;width:441px;font-size:13.4px;line-height:25.6px;color:var(--text);text-align:justify}
.about-copy p+p{margin-top:25px}
.about-btn{left:648px;top:1237px;width:163px;height:48px}

/* services */
.service{position:absolute;width:438px;height:438px;border-radius:50%;border:17px solid var(--orange);background:var(--white);text-align:center}
.service.featured{border-color:var(--grey-ring);background:radial-gradient(circle at 50% 40%,#f3f1ee 0%,#dcdad6 60%,#c7c5c1 100%)}
.svc-icon{position:absolute;width:86px;height:86px;border-radius:50%;background:var(--orange)}
.svc-title{position:absolute;width:400px;text-align:center;font-weight:700;font-size:20.5px;color:var(--ink);letter-spacing:.3px;white-space:nowrap}
.svc-copy{position:absolute;width:320px;text-align:center;font-size:13.4px;line-height:25.6px;color:var(--text)}
.svc-btn{width:164px;height:47px}

/* projects */
.project{position:absolute}
.eye{left:572px;top:2204px;width:56px;height:56px;border-radius:50%;background:var(--orange)}

/* testimonial */
.band{left:0;top:2813px;width:1200px;height:321px;background:var(--orange)}
.testi-photo{left:520px;top:2760px;width:567px;height:417px;background:linear-gradient(180deg,#1d2736 0%,#2b3440 40%,#5a4b35 70%,#1e1e1e 100%)}
.testi-card{left:111px;top:2912px;width:489px;height:267px;background:var(--white)}
.testi-title{left:141px;top:2942px;font-size:29px}
.testi-rule{left:141px;top:2991px;width:63px;height:4px;background:var(--orange)}
.quote{left:145px;top:3013px;width:422px;font-size:13.4px;font-style:italic;line-height:25.6px;color:var(--text);text-align:justify}
.author{left:148px;top:3130px;font-size:18px;font-weight:500;color:#333}
.company{left:148px;top:3160px;font-size:13px;color:var(--text)}
.testi-arrows{left:474px;top:3149px}

/* news */
.news-img{position:absolute;top:3408px;width:310px;height:232px}
.news-date{position:absolute;top:3659px;font-size:13.4px;color:#333;display:flex;align-items:center;gap:6px}
.news-title{position:absolute;top:3695px;width:284px;padding-left:20px;border-left:4px solid var(--orange);font-weight:700;font-size:19.5px;line-height:30px;color:var(--ink);white-space:nowrap}
.news-copy{position:absolute;top:3750px;width:292px;font-size:13.4px;line-height:25.6px;color:var(--text)}
.news-link{position:absolute;top:3839px;font-size:13.4px;font-weight:700;color:var(--orange);text-decoration:underline;display:flex;align-items:center;gap:4px}

/* footer */
.footer{left:0;top:3958px;width:1200px;height:444px;background:radial-gradient(circle at 52% 20%,#3a332c 0%,#232325 45%,#1a1a1c 100%)}
.foot-brand{left:147px;top:4108px;color:var(--orange);font-family:'Montserrat',Arial,sans-serif;font-weight:700;text-align:center;width:202px;line-height:1}
.foot-brand .name{font-size:33px;letter-spacing:1px}
.foot-brand .sub{font-size:16px;letter-spacing:2.6px;margin-top:6px}
.social{position:absolute;top:4201px;width:30px;height:30px;border-radius:50%;border:1.5px solid var(--white)}
.foot-head{position:absolute;top:4053px;color:var(--white);font-family:'Montserrat',Arial,sans-serif;font-weight:700;font-size:16px;letter-spacing:.5px}
.foot-list{position:absolute;top:4098px;list-style:none;color:var(--white);font-size:13.4px;line-height:27.3px}
.contact-item{position:absolute;left:843px;color:var(--white);font-size:13.4px}
.contact-item .k{font-weight:700;font-size:11.5px;padding-left:36px}
.contact-item .v{padding-left:36px;line-height:20px;margin-top:3px;white-space:nowrap}
.contact-item svg{position:absolute;left:12px;top:0}
.to-top{left:1111px;top:4269px;width:34px;height:34px;border-radius:50%;background:var(--orange)}
.copyright{left:0;top:4320px;width:1200px;text-align:center;color:var(--white);font-size:14px}
</style>
</head>
<body>

<!-- HERO -->
<div class="abs hero" role="img" aria-label="Modern white house with glowing windows on a lawn at sunset"></div>
<div class="abs brand"><div class="name">FENWICK</div><div class="sub">GRADING LTD</div></div>
<nav class="abs nav">
  <a class="active" style="left:0">Home</a>
  <a style="left:68px">About Us</a>
  <a style="left:157px">Services <svg width="10" height="6" viewBox="0 0 10 6"><path d="M0 0h10L5 6z" fill="#fff"/></svg></a>
  <a style="left:253px">Blog</a>
  <a style="left:309px">Contact</a>
</nav>
<div class="abs call">
  <div class="ring"></div>
  <svg class="abs" style="left:57px;top:37px" width="18" height="18" viewBox="0 0 24 24"><path d="M6.6 10.8a15.1 15.1 0 0 0 6.6 6.6l2.2-2.2c.3-.3.7-.4 1-.2 1.1.4 2.3.6 3.6.6.6 0 1 .4 1 1V20c0 .6-.4 1-1 1A17 17 0 0 1 3 4c0-.6.4-1 1-1h3.5c.6 0 1 .4 1 1 0 1.2.2 2.4.6 3.6.1.3 0 .7-.2 1z" fill="#F0912C"/></svg>
  <div class="lbl">Call Us Today :</div>
  <div class="num">+1 555 014 2290</div>
</div>
<h1 class="abs heading hero-title">FENWICK<br>GRADING</h1>
<div class="btn hero-btn">Get Started</div>
<svg class="abs slider-arrows" width="80" height="32" viewBox="0 0 80 32"><path d="M30 2 0 16l30 14z" fill="#fff"/><path d="M44 2l30 14-30 14z" fill="#F0912C"/></svg>

<!-- ABOUT -->
<div class="photo about-main" role="img" aria-label="Workers in hard hats laying shingles at dusk"></div>
<div class="photo about-small" role="img" aria-label="Dark timber house with solar panels beside a lit pool"></div>
<div class="abs badge"><b>25</b><span>Years<br>Experience</span></div>
<div class="abs about-box"></div>
<h2 class="abs heading about-title">ABOUT US</h2>
<div class="abs about-rule"></div>
<div class="abs about-copy">
  <p>Lorem ipsum dolor sit amet, consectetur adipiscing elit, sed do eiusmod tempor incididunt ut labore et dolore magna aliqua. Ut enim ad minim veniam, quis nostrud exercitation ullamco laboris nisi ut aliquip ex ea commodo consequat.</p>
  <p>Duis aute irure dolor in reprehenderit in voluptate velit esse cillum dolore eu fugiat nulla pariatur.Lorem ipsum dolor sit amet, consectetur adipiscing elit, sed do eiusmod tempor incididunt</p>
</div>
<div class="btn about-btn">Learn More <svg class="chev" viewBox="0 0 12 12"><circle cx="6" cy="6" r="6" fill="#fff"/><path d="M5 3.5 7.5 6 5 8.5" stroke="#F0912C" stroke-width="1.6" fill="none"/></svg></div>

<!-- SERVICES -->
<h2 class="heading section-title" style="top:1378px">OUR SERVICES</h2>
<div class="title-rule" style="top:1439px"></div>

<div class="service" style="left:-19px;top:1469px"></div>
<div class="service featured" style="left:381px;top:1469px" role="img" aria-label="Technician in hi-vis vest installing lighting, softly faded"></div>
<div class="service" style="left:781px;top:1469px"></div>

<div class="svc-icon" style="left:157px;top:1538px"></div>
<svg class="abs" style="left:178px;top:1559px" width="44" height="44" viewBox="0 0 44 44" fill="none" stroke="#fff" stroke-width="2"><rect x="6" y="6" width="32" height="32"/><path d="M6 38 38 6M14 30h10M30 14v10"/></svg>
<div class="svc-icon" style="left:557px;top:1538px"></div>
<svg class="abs" style="left:578px;top:1559px" width="44" height="44" viewBox="0 0 44 44" fill="none" stroke="#fff" stroke-width="2"><path d="M22 4v8M14 20a8 8 0 0 1 16 0v6H14zM10 26h24v8H10zM16 34v6h12v-6"/></svg>
<div class="svc-icon" style="left:957px;top:1538px"></div>
<svg class="abs" style="left:978px;top:1559px" width="44" height="44" viewBox="0 0 44 44" fill="none" stroke="#fff" stroke-width="2"><path d="M6 16 10 6h24l4 10zM8 16v22h28V16M16 38V26h12v12M6 16h32"/></svg>

<div class="svc-title" style="left:0;top:1640px">IRRIGATION INSTALLS</div>
<div class="svc-title" style="left:400px;top:1640px">LANDSCAPE LIGHTING</div>
<div class="svc-title" style="left:800px;top:1640px">BURIED WIRE &amp; DRAINAGE</div>

<div class="svc-copy" style="left:40px;top:1682px">Lorem ipsum dolor sit amet, consectetur adipiscing elit, sed do eiusmod tempor incididunt ut labore et dolore magna aliqua.</div>
<div class="svc-copy" style="left:440px;top:1682px">Lorem ipsum dolor sit amet, consectetur adipiscing elit, sed do eiusmod tempor incididunt ut labore et dolore magna aliqua.</div>
<div class="svc-copy" style="left:840px;top:1682px">Lorem ipsum dolor sit amet, consectetur adipiscing elit, sed do eiusmod tempor incididunt ut labore et dolore magna aliqua.</div>

<div class="btn svc-btn" style="left:118px;top:1783px">Learn More <svg class="chev" viewBox="0 0 12 12"><circle cx="6" cy="6" r="6" fill="#fff"/><path d="M5 3.5 7.5 6 5 8.5" stroke="#F0912C" stroke-width="1.6" fill="none"/></svg></div>
<div class="btn svc-btn" style="left:519px;top:1783px">Learn More <svg class="chev" viewBox="0 0 12 12"><circle cx="6" cy="6" r="6" fill="#fff"/><path d="M5 3.5 7.5 6 5 8.5" stroke="#F0912C" stroke-width="1.6" fill="none"/></svg></div>
<div class="btn svc-btn" style="left:920px;top:1783px">Learn More <svg class="chev" viewBox="0 0 12 12"><circle cx="6" cy="6" r="6" fill="#fff"/><path d="M5 3.5 7.5 6 5 8.5" stroke="#F0912C" stroke-width="1.6" fill="none"/></svg></div>

<!-- PROJECTS -->
<h2 class="heading section-title" style="top:1999px">OUR PROJECTS</h2>
<div class="title-rule" style="top:2059px"></div>
<div class="project" style="left:111px;top:2095px;width:316px;height:274px;background:linear-gradient(160deg,#c9c6bf 0%,#3b3d42 45%,#d9a864 60%,#8a8a88 100%)" role="img" aria-label="Modern gabled glass house with lit interior"></div>
<div class="project" style="left:441px;top:2095px;width:318px;height:274px;background:linear-gradient(170deg,#5d7d9c 0%,#34465a 45%,#9a6a3c 65%,#1f2a35 100%)" role="img" aria-label="Glass apartment building reflected in water at dusk"></div>
<div class="eye abs"></div>
<svg class="abs" style="left:588px;top:2222px" width="24" height="20" viewBox="0 0 24 20"><path d="M1 10C5 3 19 3 23 10 19 17 5 17 1 10z" fill="#fff"/><circle cx="12" cy="10" r="4" fill="#F0912C"/></svg>
<div class="project" style="left:771px;top:2095px;width:318px;height:274px;background:linear-gradient(180deg,#8e9ab8 0%,#b89aa0 35%,#45433f 60%,#56683a 100%)" role="img" aria-label="Dark two-storey family house on a green lawn"></div>
<div class="project" style="left:111px;top:2382px;width:482px;height:274px;background:linear-gradient(135deg,#b98a55 0%,#d8a86c 40%,#c4c4c4 60%,#9d6b3f 100%)" role="img" aria-label="Hands wiring an electrical socket on a workbench with cable and tools"></div>
<div class="project" style="left:607px;top:2382px;width:482px;height:274px;background:linear-gradient(120deg,#e8ebee 0%,#7a8590 35%,#2c2f33 55%,#d8d4cc 80%,#e2802e 100%)" role="img" aria-label="Technician in orange hard hat working on a cable enclosure"></div>

<!-- TESTIMONIAL -->
<div class="abs band"></div>
<div class="photo testi-photo" role="img" aria-label="Modern house entrance lit at night with a lit pathway"></div>
<div class="abs testi-card"></div>
<h2 class="abs heading testi-title">WHAT OUR CLIENTS SAY</h2>
<div class="abs testi-rule"></div>
<p class="abs quote">"Lorem ipsum dolor sit amet, consectetur adipiscing elit, sed do eiusmod tempor incididunt ut labore et dolore magna aliqua. Ut enim ad minim veniam, quis nostrud exercitation ullamco laboris nisi ut aliquip ex ea commodo consequat. "</p>
<div class="abs author">John Doe</div>
<div class="abs company">Company name</div>
<svg class="abs testi-arrows" width="76" height="24" viewBox="0 0 76 24" fill="none" stroke-width="2.4"><path d="M32 12H4M12 4 4 12l8 8" stroke="#bbb"/><path d="M44 12h28M64 4l8 8-8 8" stroke="#F0912C"/></svg>

<!-- NEWS -->
<h2 class="heading section-title" style="top:3310px">NEWS &amp; UPDATE</h2>
<div class="title-rule" style="top:3370px"></div>

<div class="news-img" style="left:111px;background:linear-gradient(160deg,#3b3e44 0%,#8a8f92 40%,#6bc26a 70%,#3f8e45 100%)" role="img" aria-label="Cable splicing machine in a green case"></div>
<div class="news-img" style="left:446px;background:linear-gradient(135deg,#e9e6e1 0%,#f3b43d 40%,#c58a5a 60%,#ececec 100%)" role="img" aria-label="Electrician in gloves handling bundled coloured cables"></div>
<div class="news-img" style="left:779px;background:linear-gradient(180deg,#2e4560 0%,#6a7b90 40%,#c99a62 60%,#2e4b63 100%)" role="img" aria-label="Modern villa with a lit swimming pool at dusk"></div>

<div class="news-date" style="left:126px"><svg width="13" height="13" viewBox="0 0 13 13"><rect x="1" y="2" width="11" height="10" fill="none" stroke="#333" stroke-width="1.4"/><path d="M1 5h11M4 0v3M9 0v3" stroke="#333" stroke-width="1.4"/></svg>Jan 20, 2022</div>
<div class="news-date" style="left:461px"><svg width="13" height="13" viewBox="0 0 13 13"><rect x="1" y="2" width="11" height="10" fill="none" stroke="#333" stroke-width="1.4"/><path d="M1 5h11M4 0v3M9 0v3" stroke="#333" stroke-width="1.4"/></svg>Jan 20, 2022</div>
<div class="news-date" style="left:795px"><svg width="13" height="13" viewBox="0 0 13 13"><rect x="1" y="2" width="11" height="10" fill="none" stroke="#333" stroke-width="1.4"/><path d="M1 5h11M4 0v3M9 0v3" stroke="#333" stroke-width="1.4"/></svg>Jan 20, 2022</div>

<div class="news-title" style="left:128px">Lorem ipsum dolor sit am<br>et, consectetur</div>
<div class="news-title" style="left:463px">Lorem ipsum dolor sit am<br>et, consectetur</div>
<div class="news-title" style="left:797px">Lorem ipsum dolor sit am<br>et, consectetur</div>

<p class="news-copy" style="left:128px">Lorem ipsum dolor sit amet, consect etur adipiscing elit, sed do eiusmod tempor incididunt ut</p>
<p class="news-copy" style="left:463px">Lorem ipsum dolor sit amet, consect etur adipiscing elit, sed do eiusmod tempor incididunt ut</p>
<p class="news-copy" style="left:797px">Lorem ipsum dolor sit amet, consect etur adipiscing elit, sed do eiusmod tempor incididunt ut</p>

<div class="news-link" style="left:128px">LEARN MORE <svg width="12" height="12" viewBox="0 0 12 12"><circle cx="6" cy="6" r="6" fill="#F0912C"/><path d="M5 3.5 7.5 6 5 8.5" stroke="#fff" stroke-width="1.6" fill="none"/></svg></div>
<div class="news-link" style="left:463px">LEARN MORE <svg width="12" height="12" viewBox="0 0 12 12"><circle cx="6" cy="6" r="6" fill="#F0912C"/><path d="M5 3.5 7.5 6 5 8.5" stroke="#fff" stroke-width="1.6" fill="none"/></svg></div>
<div class="news-link" style="left:797px">LEARN MORE <svg width="12" height="12" viewBox="0 0 12 12"><circle cx="6" cy="6" r="6" fill="#F0912C"/><path d="M5 3.5 7.5 6 5 8.5" stroke="#fff" stroke-width="1.6" fill="none"/></svg></div>

<!-- FOOTER -->
<footer class="abs footer"></footer>
<div class="abs foot-brand"><div class="name">FENWICK</div><div class="sub">GRADING LTD</div></div>
<div class="social" style="left:204px"></div>
<div class="social" style="left:245px"></div>
<div class="social" style="left:286px"></div>

<div class="foot-head" style="left:432px">QUICK LINKS</div>
<ul class="foot-list" style="left:433px"><li>Home</li><li>About us</li><li>Our Services</li><li>News</li><li>Contact Us</li></ul>
<div class="foot-head" style="left:614px">ABOUT COMPANY</div>
<ul class="foot-list" style="left:613px"><li>Legal Information</li><li>Terms &amp; Condition</li><li>Privacy Policy</li><li>Support</li><li>Site Map</li></ul>
<div class="foot-head" style="left:843px">CONTACT US</div>

<div class="contact-item" style="top:4096px">
  <svg width="14" height="14" viewBox="0 0 24 24"><path d="M6.6 10.8a15.1 15.1 0 0 0 6.6 6.6l2.2-2.2c.3-.3.7-.4 1-.2 1.1.4 2.3.6 3.6.6.6 0 1 .4 1 1V20c0 .6-.4 1-1 1A17 17 0 0 1 3 4c0-.6.4-1 1-1h3.5c.6 0 1 .4 1 1 0 1.2.2 2.4.6 3.6.1.3 0 .7-.2 1z" fill="#F0912C"/></svg>
  <div class="k">Phone</div><div class="v">+1 (555) 014-2290</div>
</div>
<div class="contact-item" style="top:4148px">
  <svg width="14" height="12" viewBox="0 0 14 12"><rect width="14" height="12" rx="1" fill="#F0912C"/><path d="M1 2l6 4.5L13 2" stroke="#1d1d1f" stroke-width="1.3" fill="none"/></svg>
  <div class="k">Email</div><div class="v">fenwickgrading@mailbox-example.net</div>
</div>
<div class="contact-item" style="top:4199px">
  <svg width="12" height="16" viewBox="0 0 12 16"><path d="M6 0a6 6 0 0 0-6 6c0 4.5 6 10 6 10s6-5.5 6-10a6 6 0 0 0-6-6z" fill="#F0912C"/><circle cx="6" cy="6" r="2.2" fill="#1d1d1f"/></svg>
  <div class="k">Location</div><div class="v">311 S Lorem ipsum dolor sit amet,<br>consectetur adipiscing elit,</div>
</div>

<div class="abs to-top"></div>
<svg class="abs" style="left:1120px;top:4279px" width="16" height="12" viewBox="0 0 16 12"><path d="M2 9l6-6 6 6" stroke="#fff" stroke-width="2" fill="none"/></svg>
<div class="abs copyright">2024 Copyrights Company name &nbsp;| All Rights Reserved</div>

</body>
</html>
```